Automotive component supplier needs a business card design

We need a business card design for our company called Velran Global Components Ltd based in the UK. We are a supplier of interior and exterior components to premium car manufacturers such as Corvel Ashby, Hadley Fenn, Marquist and Tavarelli. We would like to see a modern business card design that uses the colour blue.

Target Market(s)

Premium automotive car manufacturers.

Industry/Entity Type

Automotive

Contact Information for Business Card

Company Name : Velran Global Components Limited
Address: 17 Marlow Yard, Upper Heath, Warwick, CV31 8QL, United Kingdom
Web Address : www.velrancomponents-example.co.uk

Font styles to use
Other font styles liked:
• Helvetica

Colors
3176b5
0255a3
85acd3
cfdeed
cee9f5
85cae6
34a6d7
0692cd
9bcb3c

Requirements
Must have
• Clear company logo and a mixture of blue colours.
Nice to have
• A high quality modern image.
Should not have
• Multiple colours.

```html
<!DOCTYPE html>
<html lang="en">
<head>
<meta charset="utf-8">
<title>Velran Global Components – Business Card</title>
<link href="https://fonts.googleapis.com/css2?family=Lato:wght@400;700;900&display=swap" rel="stylesheet">
<style>
  :root {
    --brand-blue: #0692cd;
    --deep-blue: #0a86c8;
    --accent-green: #9bcb3c;
    --ink: #1e2a33;
    --paper: #ffffff;
    --backdrop: #e9edf0;
  }
  * { box-sizing: border-box; margin: 0; padding: 0; }
  html, body { width: 1200px; height: 800px; overflow: hidden; }
  body {
    background: var(--backdrop);
    font-family: "Lato", Helvetica, Arial, sans-serif;
    position: relative;
  }
  .card {
    position: absolute;
    width: 560px;
    height: 320px;
    overflow: hidden;
    box-shadow: 0 6px 20px rgba(0,0,0,0.15);
  }

  .wordmark {
    display: flex;
    align-items: center;
    gap: 10px;
    white-space: nowrap;
  }
  .wordmark-name {
    font-weight: 900;
    text-transform: uppercase;
    letter-spacing: 0.5px;
  }
  .wordmark-square {
    background: var(--accent-green);
    flex: none;
  }

  /* Back of card */
  .card-back {
    left: 60px; top: 60px;
    background: var(--brand-blue);
    color: var(--paper);
  }
  .card-back .wordmark {
    position: absolute;
    left: 0; right: 0; top: 118px;
    justify-content: center;
  }
  .card-back .wordmark-name { font-size: 28px; }
  .card-back .wordmark-square { width: 13px; height: 13px; }
  .card-back .website {
    position: absolute;
    left: 0; right: 0; bottom: 30px;
    text-align: center;
    font-size: 14px;
    letter-spacing: 1.5px;
  }

  /* Front of card */
  .card-front {
    left: 580px; top: 420px;
    background: var(--paper);
    color: var(--ink);
  }
  .card-front .wordmark {
    position: absolute;
    left: 34px; top: 48px;
    color: var(--brand-blue);
  }
  .card-front .wordmark-name { font-size: 18px; }
  .card-front .wordmark-square { width: 10px; height: 10px; }

  .person {
    position: absolute;
    right: 50px; top: 100px;
    text-align: right;
  }
  .person-name {
    color: var(--brand-blue);
    font-weight: 700;
    font-size: 22px;
    line-height: 1.1;
  }
  .person-role { font-size: 14px; margin-top: 2px; }

  .divider {
    position: absolute;
    left: 22px; right: 50px; top: 152px;
    height: 2px;
    background: var(--brand-blue);
  }
  .address {
    position: absolute;
    right: 50px; top: 166px;
    text-align: right;
    font-size: 14px;
    font-style: normal;
    line-height: 1.35;
  }
  .contacts {
    position: absolute;
    left: 30px; top: 196px;
    list-style: none;
    font-size: 15px;
    line-height: 1.45;
  }
  .contacts li { display: flex; align-items: center; gap: 10px; }
  .contacts svg { width: 14px; height: 14px; fill: var(--brand-blue); flex: none; }

  .bottom-band {
    position: absolute;
    left: 0; right: 0; bottom: 0;
    height: 22px;
    background: var(--accent-green);
  }
  .web-tab {
    position: absolute;
    right: 0; bottom: 0;
    width: 262px; height: 50px;
    background: var(--deep-blue);
    border-top-left-radius: 40px 50px;
    color: var(--paper);
    font-size: 12.5px;
    display: flex; align-items: center; justify-content: flex-end;
    padding-right: 16px;
  }
</style>
</head>
<body>

  <section class="card card-back" aria-label="Business card, back">
    <div class="wordmark">
      <span class="wordmark-name">Velran Global Components</span>
      <span class="wordmark-square"></span>
    </div>
    <p class="website">www.velrancomponents-example.co.uk</p>
  </section>

  <section class="card card-front" aria-label="Business card, front">
    <div class="wordmark">
      <span class="wordmark-name">Velran Global Components</span>
      <span class="wordmark-square"></span>
    </div>

    <div class="person">
      <p class="person-name">Alden Marsh</p>
      <p class="person-role">Manager</p>
    </div>

    <div class="divider"></div>

    <address class="address">
      17 Marlow Yard, Upper Heath<br>
      Warwick, CV31 8QL<br>
      United Kingdom
    </address>

    <ul class="contacts">
      <li>
        <svg viewBox="0 0 24 24" aria-hidden="true"><path d="M6.6 10.8a15.1 15.1 0 0 0 6.6 6.6l2.2-2.2c.3-.3.7-.4 1-.2 1.1.4 2.3.6 3.6.6.6 0 1 .4 1 1V20c0 .6-.4 1-1 1A17 17 0 0 1 3 4c0-.6.4-1 1-1h3.5c.6 0 1 .4 1 1 0 1.3.2 2.5.6 3.6.1.3 0 .7-.2 1z"/></svg>
        <span>512 004 2930</span>
      </li>
      <li>
        <svg viewBox="0 0 24 24" aria-hidden="true"><path d="M7 1h10a2 2 0 0 1 2 2v18a2 2 0 0 1-2 2H7a2 2 0 0 1-2-2V3a2 2 0 0 1 2-2zm0 3v14h10V4zm5 15.5a1.2 1.2 0 1 0 0 2.4 1.2 1.2 0 0 0 0-2.4z"/></svg>
        <span>512 004 2931</span>
      </li>
      <li>
        <svg viewBox="0 0 24 24" aria-hidden="true"><path d="M2 5h20v14H2zm2 2v.5l8 5 8-5V7zm0 2.8V17h16V9.8l-8 5z"/></svg>
        <span>info@velrancomponents-example.co.uk</span>
      </li>
    </ul>

    <div class="bottom-band"></div>
    <div class="web-tab">www.velrancomponents-example.co.uk</div>
  </section>

</body>
</html>
```